Business Card Design Project

We are a construction company in Orange County, CA. We need a two sided business card. We would like the back to be our logo with web URL. Front should included Name, title, address, phone, fax and email address.

our address is
627 West Dorrance Blvd, Suite 308
Anaheim, CA 92718

Our logo files are attached.

Construction

```html
<!DOCTYPE html>
<html lang="en">
<head>
<meta charset="utf-8">
<title>Halvor Business Card</title>
<link rel="stylesheet" href="https://fonts.googleapis.com/css2?family=Source+Sans+3:ital,wght@0,400;0,600;0,700;1,700&display=swap">
<style>
  :root {
    --brand-blue: #124a7e;
    --rule-grey: #b4b6b9;
    --ink: #3b3b3b;
    --card: #ffffff;
    --backdrop: #e4e5e7;
  }
  html, body {
    margin: 0;
    width: 960px;
    height: 1200px;
    overflow: hidden;
    background: var(--backdrop);
    font-family: "Source Sans 3", sans-serif;
  }
  .card {
    position: absolute;
    width: 840px;
    height: 480px;
    background: var(--card);
    border-radius: 28px;
    overflow: hidden;
    box-shadow: 0 3px 8px rgba(0,0,0,0.18);
  }
  .card-front { left: 66px; top: 100px; }
  .card-back { left: 55px; top: 643px; }
  .edge-band {
    position: absolute;
    left: 0; right: 0; bottom: 0;
    height: 14px;
    background: var(--brand-blue);
  }
  .edge-rule {
    position: absolute;
    left: 0; right: 0; bottom: 14px;
    height: 4px;
    background: var(--rule-grey);
  }
  .wordmark {
    position: absolute;
    left: 0; right: 0;
    text-align: center;
    color: var(--brand-blue);
    font-weight: 700;
    line-height: 1;
    margin: 0;
  }
  .card-front .wordmark { top: 76px; font-size: 140px; letter-spacing: 2px; }
  .card-back .wordmark { top: 130px; font-size: 188px; letter-spacing: 3px; }
  .contact {
    position: absolute;
    left: 0; right: 0;
    top: 284px;
    text-align: center;
    color: var(--ink);
  }
  .contact p { margin: 0; font-size: 20px; line-height: 38px; }
  .contact .person { font-size: 26px; font-weight: 600; line-height: 36px; margin-bottom: 8px; }
  .contact .role { font-size: 20px; }
  .contact .label { font-weight: 700; font-style: italic; }
  .web-address {
    position: absolute;
    left: 0; right: 0;
    top: 400px;
    text-align: center;
    margin: 0;
    font-size: 31px;
    font-weight: 700;
    color: var(--ink);
  }
</style>
</head>
<body>
  <section class="card card-front">
    <div class="edge-rule"></div>
    <div class="edge-band"></div>
    <h1 class="wordmark">HALVOR</h1>
    <div class="contact">
      <p class="person">Your Name, <span class="role">Designation</span></p>
      <p><span class="label">e</span> : info@halvorbuild.com &nbsp;|&nbsp; <span class="label">w</span> : www.halvorbuild.com</p>
      <p><span class="label">p</span> : 1-555-0142 &nbsp;|&nbsp; <span class="label">f</span> : 1-555-0142</p>
      <p>627 West Dorrance Blvd, Suite 308, Anaheim, CA 92718</p>
    </div>
  </section>

  <section class="card card-back">
    <h2 class="wordmark">HALVOR</h2>
    <p class="web-address">www.halvorbuild.com</p>
  </section>
</body>
</html>
```